Stationary design for boutique production house

We need a stationary design for our production house, 'Lorno Productions' based in Singapore. We produce microfilms as well as podcasts, talkshows and events. Our logo is a stylized icon of our director, who is also the executive producer and host of our programs, Lorno. Our main company colors are Red, Black and white. We would like a clean, minimalist design incorporating our existing company logo that conveys a sense of urbanism and elegance.

Logo and font files are attached. f

Target Market(s)

We focus on lifestyle media rather than entertainment.

Industry/Entity Type

Boutique

Font styles to use
Serif
Sans Serif

Colors
ec1f27
ffffff
000000

Requirements
Must have
• Our company logo and at least one of our company colors.
Nice to have
• Our address and contact information.
Should not have
• Changes made to the company logo (using only certain parts of it is fine though)

```html
<!DOCTYPE html>
<html lang="en">
<head>
<meta charset="utf-8">
<title>Lorno Productions – Business Card</title>
<link rel="stylesheet" href="https://fonts.googleapis.com/css2?family=Jost:wght@400;500&family=Bodoni+Moda:wght@500&display=swap">
<style>
  :root {
    --brand-red: #ec1f27;
    --brand-white: #ffffff;
    --brand-black: #1d1b1c;
    --backdrop: #3b3b3b;
    --rule-grey: #8a8a8a;
  }
  * { margin: 0; padding: 0; box-sizing: border-box; }
  html, body {
    width: 1200px;
    height: 659px;
    overflow: hidden;
    background: var(--backdrop);
  }
  .stage {
    width: 1200px;
    height: 659px;
    display: flex;
    justify-content: center;
    align-items: center;
    gap: 90px;
  }
  .card {
    width: 320px;
    height: 560px;
    position: relative;
    overflow: hidden;
  }

  /* Front: contact side */
  .card--contact {
    background: var(--brand-red);
    color: var(--brand-white);
    font-family: "Jost", sans-serif;
    text-align: center;
  }
  .contact-block {
    position: absolute;
    top: 58px;
    left: 0;
    right: 0;
  }
  .holder-name {
    font-size: 22px;
    font-weight: 500;
    letter-spacing: 1px;
  }
  .holder-role {
    display: flex;
    align-items: center;
    justify-content: center;
    gap: 6px;
    margin-top: 4px;
    font-size: 13px;
    letter-spacing: 0.5px;
  }
  .holder-role .rule {
    width: 70px;
    height: 1px;
    background: var(--brand-white);
    position: relative;
  }
  .holder-role .rule::after {
    content: "";
    position: absolute;
    top: -2px;
    width: 5px;
    height: 5px;
    border-radius: 50%;
    background: var(--brand-white);
  }
  .holder-role .rule--left::after { right: 0; }
  .holder-role .rule--right::after { left: 0; }
  .address {
    margin-top: 14px;
    font-size: 12.5px;
    line-height: 1.45;
  }
  .phones {
    margin-top: 2px;
    font-size: 12.5px;
    line-height: 1.45;
  }
  .web {
    margin-top: 2px;
    font-size: 12.5px;
    letter-spacing: 5px;
  }
  .contact-wordmark {
    position: absolute;
    left: 0;
    right: 0;
    bottom: 0;
    height: 250px;
    background: var(--brand-white);
    border-radius: 160px 160px 0 0;
    display: flex;
    flex-direction: column;
    align-items: center;
    justify-content: center;
    gap: 14px;
  }
  .contact-wordmark .name {
    font-family: "Jost", sans-serif;
    font-weight: 500;
    font-size: 52px;
    letter-spacing: 3px;
    color: var(--brand-red);
  }
  .contact-wordmark .dot {
    width: 22px;
    height: 22px;
    border-radius: 50%;
    background: var(--brand-red);
  }

  /* Back: brand side */
  .card--brand {
    background: var(--brand-white);
    color: var(--brand-black);
  }
  .brand-lockup {
    position: absolute;
    top: 110px;
    left: 0;
    right: 0;
    display: flex;
    flex-direction: column;
    align-items: center;
    gap: 16px;
  }
  .brand-lockup .dot {
    width: 14px;
    height: 14px;
    border-radius: 50%;
    background: var(--brand-red);
  }
  .brand-lockup .name {
    font-family: "Bodoni Moda", serif;
    font-weight: 500;
    font-size: 30px;
    letter-spacing: 1.5px;
    text-transform: uppercase;
    color: var(--brand-black);
    text-align: center;
    line-height: 1.15;
  }
  .brand-lockup .rule {
    width: 200px;
    height: 1px;
    background: var(--rule-grey);
  }
  .brand-faint {
    position: absolute;
    left: 0;
    right: 0;
    bottom: 0;
    height: 220px;
    background: #ebebeb;
    border-radius: 160px 160px 0 0;
    display: flex;
    align-items: center;
    justify-content: center;
  }
  .brand-faint .name {
    font-family: "Bodoni Moda", serif;
    font-weight: 500;
    font-size: 54px;
    letter-spacing: 3px;
    text-transform: uppercase;
    color: #dcdcdc;
  }
</style>
</head>
<body>
  <main class="stage">
    <section class="card card--contact" aria-label="Contact side">
      <div class="contact-block">
        <h1 class="holder-name">MARA QUELL</h1>
        <p class="holder-role">
          <span class="rule rule--left"></span>
          CEO/FOUNDER
          <span class="rule rule--right"></span>
        </p>
        <p class="address">12 Keong Saik Road<br>Singapore 089128</p>
        <p class="phones">P: 6221 4750 M: 9184 3306<br>F: 6221 4751 E: hello@lornoprod.com</p>
        <p class="web">www.lornoprod.com</p>
      </div>
      <div class="contact-wordmark">
        <span class="name">Lorno</span>
        <span class="dot"></span>
      </div>
    </section>

    <section class="card card--brand" aria-label="Brand side">
      <div class="brand-lockup">
        <span class="dot"></span>
        <p class="name">Lorno<br>Productions</p>
        <span class="rule"></span>
      </div>
      <div class="brand-faint">
        <span class="name">Lorno</span>
      </div>
    </section>
  </main>
</body>
</html>
```